Harborview Estates Business Card for Apartment Buildings

Create business cards for resident managers who run apartment buildings. The audience is the public who are searching for apartment rentals, and current residents who live at the apartment building. Key design element will be incorporating the company logo, however, the logo cannot dominate. The building name and manager name are more important than the logo. Current business card design leaves little room for copy, so we may need to reduce the size on the current card to allow for more space for copy.

Target Market(s)

Adults 18-65 years of age, who are looking for an apartment rental, plus current residents who live at our apartment buildings.

Industry/Entity Type

Property Management

Contact Information for Business Card

A major design element will be use of the company logo. Important property and manager contact information must be part of the design. The size of the logo will need to be reduced to make room for building and manager contact copy.

Font styles to use
Sans Serif

Colors
3176b5
000000
959595
ffffff

Requirements
Must have
• 1) Incorporate the company logo.
• 2) Use the company colors (dark blue, black/grey, over white).
• 3) FEATURE THE BUILDING NAME
• 4) FEATURE THE MANAGER NAME
• 5) The company name is less important than BUILDING and MANAGER
• 6) Manager contact information
• **SEE ATTACHED CREATIVE BRIEF**
Nice to have
• 1) Back of card logo watermark
• 2) Ability to write notes on back of carfd
Should not have
• Avoid letting the company logo dominate the card, the building name and manager are more important than the company logo.

```html
<!DOCTYPE html>
<html lang="en">
<head>
<meta charset="utf-8">
<title>Harborview Estates – Resident Manager Business Card</title>
<link href="https://fonts.googleapis.com/css2?family=Lato:wght@300;400;700;900&display=swap" rel="stylesheet">
<style>
  :root {
    --brand-blue: #3176b5;
    --ink: #1c1c1c;
    --grey: #959595;
    --paper: #ffffff;
    --backdrop: #8d9394;
    --rule-grey: #e3e6ea;
  }
  * { box-sizing: border-box; margin: 0; padding: 0; }
  html, body {
    width: 1200px; height: 1000px; overflow: hidden;
    background: var(--backdrop);
    font-family: "Lato", Arial, sans-serif;
  }
  .canvas { position: relative; width: 1200px; height: 1000px; }

  .card {
    position: absolute;
    background: var(--paper);
    box-shadow: 0 6px 18px rgba(0,0,0,.25);
    overflow: hidden;
  }

  /* Front */
  .card-front { left: 70px; top: 340px; width: 560px; height: 320px; }
  .front-header {
    position: absolute; left: 0; top: 0; width: 100%; height: 150px;
    border-bottom: 1px solid var(--rule-grey);
    box-shadow: 0 3px 6px rgba(0,0,0,.08);
  }
  .brand-block {
    position: absolute; left: 0; top: 45px; width: 70px; height: 105px;
    background: var(--brand-blue);
  }
  .brand-disc {
    position: absolute; left: 40px; top: 68px; width: 104px; height: 104px;
    border-radius: 50%; background: var(--paper);
    box-shadow: 0 2px 8px rgba(0,0,0,.3);
  }
  .building-name {
    position: absolute; left: 165px; top: 38px;
    color: var(--ink); line-height: 1;
  }
  .building-name .title { font-size: 36px; font-weight: 900; letter-spacing: -.5px; display: block; }
  .building-name .sub { font-size: 15px; font-weight: 700; letter-spacing: 7px; display: block; margin-top: 4px; padding-left: 30px; }
  .header-rule {
    position: absolute; left: 150px; top: 112px; width: 410px; height: 4px;
    background: var(--brand-blue);
  }
  .address {
    position: absolute; left: 185px; top: 124px;
    font-size: 13px; color: var(--ink);
  }

  .manager { position: absolute; left: 60px; top: 192px; color: #444; }
  .manager .first { font-size: 22px; font-weight: 300; letter-spacing: .5px; display: block; }
  .manager .last { font-size: 22px; font-weight: 900; color: var(--ink); display: block; }
  .manager .role { font-size: 14px; font-weight: 300; color: #666; display: block; margin-top: 2px; }

  .divider {
    position: absolute; left: 265px; top: 178px; width: 2px; height: 100px;
    background: var(--brand-blue);
  }
  .contact { position: absolute; left: 285px; top: 172px; list-style: none; font-size: 15px; color: var(--ink); line-height: 19px; }

  .company-name {
    position: absolute; right: 24px; bottom: 28px;
    font-size: 15px; font-weight: 900; color: var(--brand-blue);
    letter-spacing: .3px;
  }

  /* Back */
  .card-back { left: 770px; top: 210px; width: 330px; height: 560px; }
  .back-header {
    position: absolute; left: 0; top: 0; width: 100%; height: 120px;
    border-bottom: 1px solid var(--rule-grey);
    box-shadow: 0 3px 6px rgba(0,0,0,.08);
  }
  .back-name { position: absolute; left: 40px; top: 42px; color: var(--ink); line-height: 1; }
  .back-name .title { font-size: 31px; font-weight: 900; letter-spacing: -.5px; display: block; }
  .back-name .sub { font-size: 14px; font-weight: 700; letter-spacing: 6px; display: block; margin-top: 3px; padding-left: 16px; }
  .back-rule {
    position: absolute; left: 0; top: 120px; width: 100%; height: 12px;
    background: var(--brand-blue);
  }
  .notes-area { position: absolute; left: 0; top: 132px; width: 100%; height: 428px; }
</style>
</head>
<body>
<main class="canvas">

  <section class="card card-front" aria-label="Business card front">
    <div class="front-header">
      <div class="brand-block"></div>
      <div class="brand-disc"></div>
      <h1 class="building-name">
        <span class="title">Cedar Point</span>
        <span class="sub">APARTMENTS</span>
      </h1>
      <div class="header-rule"></div>
      <p class="address">1450 Larkspur Avenue &nbsp;|&nbsp; Bayside, CA 90210</p>
    </div>

    <div class="manager">
      <span class="first">MARISOL</span>
      <span class="last">ORTEGA</span>
      <span class="role">Resident Manager</span>
    </div>

    <div class="divider"></div>

    <ul class="contact">
      <li>O: 555-210-4400</li>
      <li>F: 555-210-4401</li>
      <li>C: 555-318-7725</li>
      <li>E: marisol@harborviewest.com</li>
    </ul>

    <p class="company-name">Harborview Estates</p>
  </section>

  <section class="card card-back" aria-label="Business card back">
    <div class="back-header">
      <h2 class="back-name">
        <span class="title">Cedar Point</span>
        <span class="sub">APARTMENTS</span>
      </h2>
    </div>
    <div class="back-rule"></div>
    <div class="notes-area" aria-label="Space for notes"></div>
  </section>

</main>
</body>
</html>
```